African homeware retailer needs a web page design

We need a web page design for a new homeware and accessories store based in Johannesburg, South Africa. Our store carries modern African inspired items from designers that support social development and poverty alleviation initiatives. We have a particular preference for outfits that are centred on the empowerment of women.

Our business celebrates the skill, design and product of African craft and the work of designers looking to take that forward in a socially beneficial way (creating employment, developing skills, supporting local crafts people etc). We aim to carry items and inspirations from all over the African continent.

We would like to see a design that communicates African beauty and elegance without the typical tribal references that are made in reference to African craft or art.

We would like the web page to be stylish, uncomplicated, modern, captivating and appealing to the discerning customer. A similar value proposition is that of http://www.marlowtenwick.example/.

This is an e-commerce website which must be attractive to both individual buyers and design professionals so the website needs to look professional.

Here are links to some websites we like:
http://www.quenbyhollis.example/
http://www.dravelo.example/

Our logo is attached to the brief.

Target Market(s)

Our target market is female, age 20-50. However should not alienate the design conscious male customer therefore

Industry/Entity Type

E-Commerce

Requirements
Must have
• - A featured product banner which includes a photograph and text. This should be easy to edit as we will be changing the featured product regularly
- An easily expendable products section with categories. Examples of categories could be cushions, bedding, crockery etc. Should be easy to add new categories as well as new product pictures
- Home/landing page should be uncluttered
- Should use the logo and should be easy to change the logo which we have in various colour combinations. We plan to change the logo colours depending on circumstance e.g. make it red and white around Valentines day (similar to the way Vintrel frequently changes the logo on their landing page)

```html
<!DOCTYPE html>
<html lang="en">
<head>
<meta charset="utf-8">
<title>Umbira Home – Homeware &amp; Accessories</title>
<link rel="stylesheet" href="https://fonts.googleapis.com/css2?family=Questrial&family=Arimo:wght@400;700&family=Noto+Serif&display=swap">
<style>
  :root {
    --brown: #55342a;
    --orange: #e4502b;
    --cream: #f5e49a;
    --yellow-band: rgba(253, 245, 160, 0.9);
    --search-btn: #fbef9a;
    --dark: #2d2d2d;
    --rule: #e2e2e2;
    --blue: #18b2ec;
    --blue-title: #1aa2dd;
    --offer: #fa6814;
    --offer-title: #e8541e;
    --green: #7fd30c;
    --green-title: #3e8a30;
    --grey-text: #555;
    --bar-bg: #f8f8f8;
    --footer-bg: #000;
    --footer-head: #cfcfcf;
    --footer-link: #a8a8a8;
    --display: "Questrial", sans-serif;
    --body: "Arimo", Arial, sans-serif;
    --serif: "Noto Serif", Georgia, serif;
  }
  * { margin: 0; padding: 0; box-sizing: border-box; }
  html, body { width: 1200px; height: 1000px; overflow: hidden; background: #fff; }
  body { position: relative; font-family: var(--body); }
  .abs { position: absolute; }
  a { text-decoration: none; color: inherit; }

  /* Header */
  .site-header { position: absolute; left: 0; top: 0; width: 1200px; height: 166px; background: var(--brown); }
  .brand { position: absolute; left: 200px; top: 95px; width: 116px; text-align: center; color: var(--orange); font-family: var(--display); }
  .brand-mark { display: block; width: 14px; height: 14px; background: var(--orange); margin: 0 auto 8px; }
  .brand-name { font-size: 17px; letter-spacing: 1.5px; line-height: 1.1; }
  .welcome { left: 700px; top: 34px; font-family: var(--display); font-size: 10px; color: #fff; font-variant: small-caps; letter-spacing: .4px; font-weight: bold; }
  .welcome a { color: var(--orange); font-size: 11px; }
  .search { left: 700px; top: 59px; width: 158px; height: 29px; background: #fff; }
  .search span { position: absolute; left: 10px; top: 10px; font-size: 7px; color: #aaa; letter-spacing: .5px; }
  .search-btn { position: absolute; right: 0; top: 0; width: 33px; height: 29px; background: var(--search-btn); }
  .search-btn svg { position: absolute; left: 10px; top: 8px; }
  .cart { left: 876px; top: 59px; width: 157px; height: 29px; background: #f1f1f1; font-family: var(--display); font-size: 10px; color: #666; font-variant: small-caps; font-weight: bold; }
  .cart span { position: absolute; left: 8px; top: 8px; }
  .cart-drop { position: absolute; right: 0; top: 0; width: 33px; height: 29px; background: #fff; }
  .cart-drop svg { position: absolute; left: 11px; top: 11px; }
  .util-nav { left: 497px; top: 104px; font-size: 8px; color: var(--cream); letter-spacing: .2px; }
  .util-nav i { font-style: normal; margin: 0 5px; }
  .header-rule { left: 497px; top: 127px; width: 536px; height: 1px; background: #3b241d; }
  .main-nav a { position: absolute; top: 140px; font-family: var(--display); font-size: 11px; color: var(--orange); font-weight: bold; letter-spacing: .5px; }

  /* Hero */
  .hero-photo { position: absolute; border-radius: 40px; }
  .photo-left { left: 222px; top: 245px; width: 235px; height: 185px; background: radial-gradient(ellipse at 50% 45%, #f1f1f1 0%, #dcdcdc 55%, rgba(255,255,255,0) 75%); }
  .photo-right { left: 535px; top: 265px; width: 350px; height: 160px; background: radial-gradient(ellipse at 50% 45%, #f3f4f7 0%, #d6dae6 50%, rgba(255,255,255,0) 78%); }
  .hero-band { left: 207px; top: 350px; width: 826px; height: 89px; background: var(--yellow-band); }
  .hero-title { left: 298px; top: 366px; font-family: var(--display); font-size: 34px; font-weight: bold; color: var(--dark); letter-spacing: 1px; line-height: 1; }
  .hero-sub { left: 302px; top: 401px; font-size: 14.5px; color: #222; }
  .hero-cta { left: 865px; top: 378px; width: 96px; height: 33px; background: var(--orange); color: #fff; font-family: var(--display); font-weight: bold; font-size: 13px; line-height: 33px; text-align: center; letter-spacing: .4px; }
  .save-badge { left: 861px; top: 229px; width: 100px; height: 100px; border-radius: 50%; background: var(--dark); color: #fff; text-align: center; }
  .save-badge .save { margin-top: 28px; font-size: 12px; line-height: 1; }
  .save-badge .save b { font-size: 22px; font-weight: 400; }
  .save-badge .note { font-size: 9.5px; line-height: 11px; margin-top: 2px; }
  .hero-rule { left: 207px; top: 454px; width: 826px; height: 1px; background: var(--rule); }

  /* Feature cards */
  .col-rule { position: absolute; top: 490px; width: 1px; height: 168px; background: var(--rule); }
  .feature-photo { position: absolute; border-radius: 6px; }
  .feature-title { position: absolute; top: 520px; font-family: var(--serif); font-size: 17px; }
  .feature-text { position: absolute; top: 555px; width: 150px; font-size: 9px; line-height: 12px; color: var(--grey-text); }
  .feature-btn { position: absolute; top: 608px; width: 90px; height: 28px; color: #fff; font-family: var(--display); font-weight: bold; font-size: 11px; line-height: 28px; text-align: center; letter-spacing: .4px; }

  /* Info bar */
  .info-bar { left: 0; top: 694px; width: 1200px; height: 54px; background: var(--bar-bg); border-top: 1px solid #e8e8e8; }
  .follow { left: 207px; top: 714px; font-family: var(--display); font-size: 17px; color: #777; letter-spacing: .6px; }
  .social { position: absolute; top: 709px; width: 28px; height: 28px; background: #333; }
  .bar-rule { position: absolute; top: 709px; width: 1px; height: 30px; background: #ddd; }
  .ship-title { left: 525px; top: 710px; font-family: var(--display); font-size: 13px; font-weight: bold; color: var(--orange); letter-spacing: .3px; }
  .ship-note { left: 525px; top: 724px; font-family: var(--display); font-size: 10px; font-weight: bold; color: #777; font-variant: small-caps; }
  .order { left: 798px; top: 715px; font-family: var(--display); font-size: 13px; font-weight: bold; color: #777; letter-spacing: .3px; }
  .order b { color: var(--orange); margin-left: 4px; }

  /* Footer */
  .site-footer { left: 0; top: 748px; width: 1200px; height: 202px; background: var(--footer-bg); }
  .foot-col { position: absolute; top: 793px; }
  .foot-col h4 { font-family: var(--display); font-size: 10.5px; color: var(--footer-head); letter-spacing: .6px; font-weight: bold; margin-bottom: 9px; }
  .foot-col li { list-style: none; font-size: 8px; color: var(--footer-link); line-height: 15.8px; }
  .newsletter { position: absolute; left: 842px; top: 816px; width: 191px; height: 26px; }
  .newsletter span { position: absolute; left: 0; top: 0; width: 147px; height: 26px; background: #3a3a3a; font-size: 7px; color: #aaa; padding: 10px 0 0 6px; }
  .newsletter b { position: absolute; right: 0; top: 0; width: 44px; height: 26px; background: var(--brown); color: #fff; font-family: var(--display); font-size: 10px; text-align: center; line-height: 26px; }
  .store { left: 842px; top: 860px; font-size: 8.5px; color: var(--footer-link); line-height: 12px; }

  .legal-bar { left: 0; top: 950px; width: 1200px; height: 50px; background: var(--brown); color: #fff; font-family: var(--display); font-size: 8px; font-weight: bold; font-variant: small-caps; letter-spacing: .3px; }
  .legal-bar .copy { position: absolute; left: 207px; top: 19px; }
  .legal-bar .terms { position: absolute; right: 167px; top: 19px; }
</style>
</head>
<body>

<header class="site-header">
  <div class="brand">
    <span class="brand-mark"></span>
    <div class="brand-name">UMBIRA HOME</div>
  </div>
  <p class="abs welcome">Welcome visitor you can <a href="#">Login</a> or <a href="#">Create an Account</a></p>
  <div class="abs search"><span>SEARCH</span>
    <div class="search-btn"><svg width="13" height="13" viewBox="0 0 13 13"><circle cx="5" cy="5" r="3.5" fill="none" stroke="#8a7a3a" stroke-width="1.6"/><line x1="7.6" y1="7.6" x2="11.5" y2="11.5" stroke="#8a7a3a" stroke-width="2"/></svg></div>
  </div>
  <div class="abs cart"><span>Cart 0 item(s) - $0.00</span>
    <div class="cart-drop"><svg width="12" height="7" viewBox="0 0 12 7"><polyline points="1,1 6,6 11,1" fill="none" stroke="#aaa" stroke-width="1"/></svg></div>
  </div>
  <nav class="abs util-nav">HOME<i>|</i>WISH LIST (0)<i>|</i>MY ACCOUNT<i>|</i>SHOPPING CART<i>|</i>CHECKOUT</nav>
  <div class="abs header-rule"></div>
  <nav class="main-nav">
    <a href="#" style="left:497px">LOREM IPSUM</a>
    <a href="#" style="left:595px">LOREM IPSUM</a>
    <a href="#" style="left:688px">LOREM IPSUM</a>
    <a href="#" style="left:781px">LOREM IPSUM</a>
    <a href="#" style="left:880px">LOREM IPSUM</a>
  </nav>
</header>

<section class="hero">
  <div class="hero-photo photo-left" role="img" aria-label="White dinner plates and bowls with black floral print"></div>
  <div class="hero-photo photo-right" role="img" aria-label="Blue-rimmed porcelain dinner set with teapot and tureen"></div>
  <div class="abs hero-band"></div>
  <h1 class="abs hero-title">CROCKERY</h1>
  <p class="abs hero-sub">A Large Selection At Competitive Price</p>
  <a href="#" class="abs hero-cta">SHOP NOW!</a>
  <div class="abs save-badge">
    <p class="save">SAVE <b>25%</b></p>
    <p class="note">On Selected<br>Products</p>
  </div>
  <div class="abs hero-rule"></div>
</section>

<section class="features">
  <div class="feature-photo" style="left:208px;top:520px;width:106px;height:70px;background:linear-gradient(135deg,#c8342c,#2a4f9a 50%,#e6b820)" role="img" aria-label="Stack of colourful striped cushions"></div>
  <h2 class="feature-title" style="left:324px;color:var(--blue-title)">Home Appliance</h2>
  <p class="feature-text" style="left:326px">Lorem ipsum dolor sit amet, consect-etur adipisicing elit, sed do eiusmod</p>
  <a href="#" class="feature-btn" style="left:327px;background:var(--blue)">LEARN MORE</a>

  <div class="col-rule" style="left:485px"></div>

  <div class="feature-photo" style="left:512px;top:527px;width:84px;height:72px;background:linear-gradient(180deg,#2a2a2a 0%,#8c8a90 40%,#c9c6cc 100%)" role="img" aria-label="Bed with striped grey bedding"></div>
  <h2 class="feature-title" style="left:603px;color:var(--offer-title)">Special Offer</h2>
  <p class="feature-text" style="left:605px">Lorem ipsum dolor sit amet, consect-etur adipisicing elit, sed do eiusmod tempor</p>
  <a href="#" class="feature-btn" style="left:606px;background:var(--offer)">VIEW DETAIL</a>

  <div class="col-rule" style="left:768px"></div>

  <div class="feature-photo" style="left:787px;top:528px;width:99px;height:60px;background:radial-gradient(ellipse,#f2f2f2 0%,#c9c9c9 60%,rgba(255,255,255,0) 80%)" role="img" aria-label="White and black patterned dinnerware set"></div>
  <h2 class="feature-title" style="left:889px;color:var(--green-title)">Free Shipping</h2>
  <p class="feature-text" style="left:890px;width:145px">on selected lorem ipsum products &amp; home appliance</p>
  <a href="#" class="feature-btn" style="left:892px;background:var(--green)">READ MORE</a>
</section>

<section class="abs info-bar"></section>
<p class="abs follow">FOLLOW US</p>
<a href="#" class="social" style="left:341px" aria-label="Social page one"></a>
<a href="#" class="social" style="left:375px" aria-label="Social page two"></a>
<div class="bar-rule" style="left:485px"></div>
<p class="abs ship-title">FREE SHIPPING</p>
<p class="abs ship-note">SHIPPING COST: On Order over $99</p>
<div class="bar-rule" style="left:768px"></div>
<p class="abs order">ORDER ONLINE <b>TEL: 1234 5678 001</b></p>

<footer class="abs site-footer"></footer>
<div class="foot-col" style="left:207px">
  <h4>MY ACCOUNT</h4>
  <ul><li>Sign In</li><li>View Cart</li><li>My Wishlist</li><li>Track My Order</li><li>Help</li></ul>
</div>
<div class="foot-col" style="left:433px">
  <h4>SITE INFO</h4>
  <ul><li>About Us</li><li>Customer Service</li><li>Privacy Policy</li><li>Site Map</li><li>Search Terms</li><li>Advanced Search</li><li>Orders and Returns</li></ul>
</div>
<div class="foot-col" style="left:638px">
  <h4>WHY BUY FOR US</h4>
  <ul><li>Shipping &amp; Returns</li><li>Secure Shopping</li><li>International Shipping</li><li>Affiliates</li><li>Group Sales</li><li>Contact Us</li></ul>
</div>
<div class="foot-col" style="left:842px"><h4>NEWSLETTER</h4></div>
<div class="newsletter"><span>Enter Your Email Address</span><b>GO</b></div>
<p class="abs store">Store Location: #1234, Lorem Ipsum Link<br>Lorem Ipsum, 2345</p>

<div class="abs legal-bar">
  <span class="copy">© 2014 Company Name. All Rights Reserved</span>
  <span class="terms">Privacy Policy &nbsp;|&nbsp; Terms &amp; Conditions</span>
</div>

</body>
</html>
```